Business Card Design

We custom build & and install Air filtration systems for mining machines - the system filters the air going into the cabin to protect the operator/driver Examples of the machines we install our units to would be Ironhaven or Veltoro. Australian owned company Our company colors are sky blue with polished Stainless steel lettering & framing. I have a logo which I will upload but I would like the new image to be crisper.

Industry/Entity Type

Business

Contact Information for Business Card

Company name - Clearlung Pty Ltd
Dale Morrissey - Position - Sales & Product Development Contact numbers Mob 0428 359 162 Tel - 07 3581 4296
Address - 147 Quarrel Rd, Wendlebury, Tarrowvale 4621, Australia

Colors
0255a3

Requirements
Must have
• sky blue & polished chrome lettering

```html
<!DOCTYPE html>
<html lang="en">
<head>
<meta charset="utf-8">
<title>Clearlung Business Card</title>
<link rel="stylesheet" href="https://fonts.googleapis.com/css2?family=Open+Sans:wght@400;600;700&display=swap">
<style>
  :root {
    --backdrop: #3b3431;
    --card: #0d0d0e;
    --card-edge: #1a1a1c;
    --brand-blue: #2f4fb0;
    --name-blue: #3553b8;
    --text-light: #e9e9ec;
    --divider: #2b2b2e;
    --chrome-light: #f2f2f4;
    --chrome-mid: #b9bcc2;
    --chrome-dark: #7d8087;
    --ink: #121212;
  }
  * { box-sizing: border-box; margin: 0; padding: 0; }
  html, body { width: 1200px; height: 900px; overflow: hidden; }
  body {
    background: var(--backdrop);
    font-family: "Open Sans", Arial, sans-serif;
    display: flex;
    align-items: center;
    justify-content: center;
    gap: 60px;
  }
  .card {
    width: 525px;
    height: 300px;
    background: var(--card);
    border: 1px solid var(--card-edge);
    border-radius: 3px;
    position: relative;
    box-shadow: 0 18px 40px rgba(0,0,0,0.45);
  }
  .card-front .brand-badge {
    position: absolute;
    left: 34px;
    top: 178px;
    width: 210px;
    height: 50px;
    background: var(--brand-blue);
    border-radius: 10px;
    display: flex;
    align-items: center;
    justify-content: center;
  }
  .brand-badge .brand-name {
    color: var(--text-light);
    font-weight: 700;
    font-size: 26px;
    letter-spacing: 0.5px;
  }
  .card-front .divider {
    position: absolute;
    left: 280px;
    top: 40px;
    width: 1px;
    height: 220px;
    background: var(--divider);
  }
  .contact {
    position: absolute;
    left: 300px;
    top: 52px;
    color: var(--text-light);
    font-size: 13px;
    line-height: 1.45;
  }
  .contact .person-name {
    color: var(--name-blue);
    font-weight: 700;
    font-size: 18px;
    line-height: 1.2;
  }
  .contact .role { margin-bottom: 26px; }
  .contact .address { margin-bottom: 16px; }
  .contact .phone-line {
    display: flex;
    align-items: center;
    gap: 8px;
  }
  .phone-line svg { width: 11px; height: 11px; fill: var(--name-blue); }
  .card-back .chrome-plate {
    position: absolute;
    left: 112px;
    top: 112px;
    width: 300px;
    height: 76px;
    border-radius: 12px;
    background: linear-gradient(120deg, var(--chrome-dark) 0%, var(--chrome-light) 30%, var(--chrome-mid) 55%, var(--chrome-light) 78%, var(--chrome-dark) 100%);
    display: flex;
    align-items: center;
    justify-content: center;
  }
  .chrome-plate .brand-name {
    color: var(--ink);
    font-weight: 700;
    font-size: 38px;
    letter-spacing: 1px;
  }
</style>
</head>
<body>
  <section class="card card-front" aria-label="Business card front">
    <div class="brand-badge">
      <span class="brand-name">Clearlung</span>
    </div>
    <div class="divider"></div>
    <div class="contact">
      <p class="person-name">Dale Morrissey</p>
      <p class="role">Sales &amp; Product Development</p>
      <p class="address">147 Quarrel Rd, Wendlebury,<br>Tarrowvale 4621, Australia</p>
      <p class="phone-line">
        <svg viewBox="0 0 24 24" aria-hidden="true"><path d="M6.6 10.8a15 15 0 0 0 6.6 6.6l2.2-2.2a1 1 0 0 1 1-.25 11.4 11.4 0 0 0 3.6.57 1 1 0 0 1 1 1V20a1 1 0 0 1-1 1A17 17 0 0 1 3 4a1 1 0 0 1 1-1h3.5a1 1 0 0 1 1 1c0 1.25.2 2.45.57 3.57a1 1 0 0 1-.25 1z"/></svg>
        0428 359 162
      </p>
      <p class="phone-line">
        <svg viewBox="0 0 24 24" aria-hidden="true"><path d="M7 1h10a2 2 0 0 1 2 2v18a2 2 0 0 1-2 2H7a2 2 0 0 1-2-2V3a2 2 0 0 1 2-2zm0 3v14h10V4zm5 15.5a1 1 0 1 0 0 2 1 1 0 0 0 0-2z"/></svg>
        07 3581 4296
      </p>
    </div>
  </section>

  <section class="card card-back" aria-label="Business card back">
    <div class="chrome-plate">
      <span class="brand-name">Clearlung</span>
    </div>
  </section>
</body>
</html>
```